Business card design - Please see revised design specs (Dec.11)

I would like to have a business card designed. I just opened my own business and am currently focusing on community benefit organizations and companies (non profit groups, etc). I need to do work that is meaningful, is authentic to me, and is limitless. My business tagline is actually Meaningful.Authentic.Limitess.

I have attached my logo as well as the background I am currently using for my website. The background does not have to be on the card. It is a reference for a design and style that I like. The logo font is Museo 300. The text can be separated from the logo. The card is full color, both sides, 3.5" x 2", bleed size 3.75 x 2.25 (0.125" bleed on all sides). My logo color is not right in the file. The CMYK color is 100/50/0/0. I require the design in AI, EPS, and press ready PDF. Convert all fonts to paths (outlined)

I will be approaching business and management professional. I want the card to communicate that I am a professional, but not stuffy. I am unique and have a strong creative side to me. I also work in a community that has a strong creative, green, and sustainability focus.

Here is my basis info:

Morton Fisk
Principal
Fernway
27 Wexley Rd.
Guelph, Ontario Canada
P4K 7T9
Cell: 555 274 9183
Email: morton@fernway.ca

```html
<!DOCTYPE html>
<html lang="en">
<head>
<meta charset="utf-8">
<title>Fernway — Business Card</title>
<link rel="stylesheet" href="https://fonts.googleapis.com/css2?family=Quicksand:wght@400;500&display=swap">
<style>
  :root {
    --page-bg: #e9e6e1;
    --brand-blue: #0a63d6;
    --blue-light: #3d8ef2;
    --blue-deep: #0c3fc4;
    --card-black: #050505;
    --text-white: #ffffff;
    --text-muted: #d6d6d6;
    --shadow: rgba(0, 0, 0, 0.22);
  }
  * { margin: 0; padding: 0; box-sizing: border-box; }
  html, body {
    width: 1200px;
    height: 1023px;
    overflow: hidden;
    background: var(--page-bg);
  }
  .sheet {
    width: 1200px;
    height: 1023px;
    display: flex;
    flex-direction: column;
    align-items: center;
    justify-content: center;
    gap: 34px;
  }
  .card {
    width: 820px;
    height: 469px;
    position: relative;
    overflow: hidden;
    box-shadow: 0 10px 28px var(--shadow);
  }

  /* Front */
  .card--front {
    background: linear-gradient(155deg, var(--blue-light) 0%, var(--brand-blue) 45%, var(--blue-deep) 100%);
  }
  .front__brand {
    position: absolute;
    left: 0;
    right: 0;
    top: 180px;
    text-align: center;
  }
  .front__name {
    font-family: "Quicksand", sans-serif;
    font-weight: 500;
    font-size: 56px;
    color: var(--text-white);
    letter-spacing: 2px;
  }
  .front__web {
    margin-top: 18px;
    font-family: "Quicksand", sans-serif;
    font-weight: 400;
    font-size: 22px;
    letter-spacing: 6px;
    color: var(--text-white);
  }

  /* Back */
  .card--back {
    background: var(--card-black);
  }
  .back__band {
    position: absolute;
    left: 0;
    top: 0;
    width: 26px;
    height: 100%;
    background: var(--brand-blue);
  }
  .back__details {
    position: absolute;
    right: 60px;
    top: 60px;
    text-align: right;
    font-family: "Quicksand", sans-serif;
    color: var(--text-white);
  }
  .back__name {
    font-size: 36px;
    font-weight: 500;
    letter-spacing: 2px;
    text-transform: uppercase;
  }
  .back__role {
    font-size: 20px;
    color: var(--text-muted);
    margin-top: 4px;
  }
  .back__company {
    font-size: 26px;
    font-weight: 500;
    color: var(--blue-light);
    text-transform: uppercase;
    letter-spacing: 2px;
    margin-top: 14px;
  }
  .back__contact {
    list-style: none;
    margin-top: 26px;
    font-size: 20px;
    line-height: 1.7;
  }
  .back__contact li {
    display: flex;
    justify-content: flex-end;
    align-items: center;
    gap: 14px;
  }
  .back__icon {
    width: 18px;
    height: 18px;
    flex: none;
  }
</style>
</head>
<body>
<main class="sheet">
  <section class="card card--front" aria-label="Card front">
    <div class="front__brand">
      <p class="front__name">Fernway</p>
      <p class="front__web">www.fernway.ca</p>
    </div>
  </section>

  <section class="card card--back" aria-label="Card back">
    <div class="back__band"></div>
    <div class="back__details">
      <h1 class="back__name">Morton Fisk</h1>
      <p class="back__role">Principal</p>
      <p class="back__company">Fernway</p>
      <ul class="back__contact">
        <li>555 274 9183
          <svg class="back__icon" viewBox="0 0 18 18"><rect width="18" height="18" rx="3" fill="#0a63d6"/><path d="M6 4.5l1.6 2.4-1 1a6 6 0 0 0 3.5 3.5l1-1L13.5 12l-1 1.6C8.5 13.5 4.5 9.5 4.4 5.5z" fill="#fff"/></svg>
        </li>
        <li>morton@fernway.ca
          <svg class="back__icon" viewBox="0 0 18 18"><rect width="18" height="18" rx="3" fill="#0a63d6"/><rect x="4" y="5.5" width="10" height="7" fill="none" stroke="#fff" stroke-width="1.2"/><path d="M4 5.5l5 4 5-4" fill="none" stroke="#fff" stroke-width="1.2"/></svg>
        </li>
        <li>27 Wexley Rd.
          <svg class="back__icon" viewBox="0 0 18 18"><rect width="18" height="18" rx="3" fill="#0a63d6"/><path d="M9 3.5a3.5 3.5 0 0 1 3.5 3.5C12.5 10 9 14.5 9 14.5S5.5 10 5.5 7A3.5 3.5 0 0 1 9 3.5z" fill="#fff"/><circle cx="9" cy="7" r="1.3" fill="#0a63d6"/></svg>
        </li>
        <li>P4K 7T9
          <svg class="back__icon" viewBox="0 0 18 18"><rect width="18" height="18" rx="3" fill="#0a63d6"/></svg>
        </li>
      </ul>
    </div>
  </section>
</main>
</body>
</html>
```